Business Card Design For Marketing Agnecy LVP

Need business card design for marketing agency.

Doug Fenwick
President, CEO
1-555-302-4196
doug@boldpromoperksgroup.example
www.BoldPromoPerksGroup.example

Back Side:
Boost Sales Using Rewards, Incentives & Giveaways
Get A Free Sample Package

Target Market(s)

B2B

Industry/Entity Type

Marketing

Contact Information for Business Card

Doug Fenwick
President, CEO
1-555-302-4196

Back Side:
Get A Free Sample Package

Please note that my current url is OLD DESIGN. I am working on new design and want the business card to match color themes at least on new site. Here is the demo link for new site so you can see the colors I use, etc.

http://layoutcratehub.example/kq/doug/lvp_final/index.html

Requirements
Must have
• Please note that my current url is OLD DESIGN. I am working on new design and want the business card to match color themes at least on new site. Here is the demo link for new site so you can see the colors I use, etc.

Nice to have

Should not have

```html
<!DOCTYPE html>
<html lang="en">
<head>
<meta charset="utf-8">
<title>LVP Business Card</title>
<link rel="stylesheet" href="https://fonts.googleapis.com/css2?family=Montserrat:wght@400;600;700;800&family=Questrial&display=swap">
<style>
  :root {
    --bg: #ececec;
    --card: #ffffff;
    --blue: #3d6eb5;
    --blue-light: #5f89c2;
    --blue-dark: #2f5a9f;
    --blue-shade: #56789f;
    --ink: #3a3a3a;
    --white: #ffffff;
  }
  * { margin: 0; padding: 0; box-sizing: border-box; }
  html, body { width: 1200px; height: 796px; overflow: hidden; background: var(--bg); }
  .canvas {
    position: relative; width: 1200px; height: 796px;
    display: flex; align-items: center; justify-content: center; gap: 40px;
  }
  .card {
    position: relative; width: 540px; height: 309px; background: var(--card);
    box-shadow: 0 10px 30px rgba(0,0,0,.12); overflow: hidden;
    font-family: "Questrial", sans-serif;
  }

  /* Back side */
  .brand {
    position: absolute; display: flex; align-items: center; gap: 12px;
    font-family: "Montserrat", sans-serif; font-weight: 800; color: var(--blue);
  }
  .brand-dot { width: 18px; height: 18px; border-radius: 50%; background: var(--blue); }
  .card-back .brand { left: 150px; top: 88px; font-size: 72px; letter-spacing: 2px; }
  .card-back .brand .brand-dot { width: 22px; height: 22px; }
  .tagline-band {
    position: absolute; left: 0; bottom: 34px; width: 312px; height: 44px;
    background: var(--blue); color: var(--white); white-space: nowrap;
    font-size: 10.5px; display: flex; align-items: center; padding-left: 14px;
  }
  .offer-box {
    position: absolute; left: 312px; bottom: 34px; width: 212px; height: 44px;
    border: 1.5px solid var(--ink); text-align: right; padding: 6px 8px 0 0; white-space: nowrap;
  }
  .offer-title { font-size: 10.5px; color: var(--ink); }
  .offer-url { font-family: "Montserrat", sans-serif; font-weight: 700; font-size: 10px; color: var(--blue); margin-top: 4px; }

  /* Front side */
  .panel { position: absolute; inset: 0; }
  .card-front .brand { left: 34px; bottom: 34px; font-size: 46px; letter-spacing: 1px; }
  .person { position: absolute; right: 40px; top: 34px; text-align: right; color: var(--white); }
  .person-name { font-family: "Montserrat", sans-serif; font-weight: 800; font-size: 25px; }
  .person-role { font-family: "Montserrat", sans-serif; font-weight: 700; font-size: 13px; margin-top: 8px; }
  .person-title { font-size: 13px; margin-top: 2px; }
  .contacts { position: absolute; right: 22px; bottom: 30px; list-style: none; color: var(--white); }
  .contacts li {
    display: flex; align-items: center; justify-content: flex-end; gap: 8px; white-space: nowrap;
    font-family: "Montserrat", sans-serif; font-weight: 700; font-size: 10.5px; margin-top: 7px;
  }
  .contacts svg { width: 12px; height: 12px; flex: none; }
</style>
</head>
<body>
<main class="canvas">

  <section class="card card-back" aria-label="Business card, back side">
    <div class="brand"><span class="brand-dot"></span>LVP</div>
    <div class="tagline-band">Boost Sales Using Rewards, Incentives &amp; Giveaways</div>
    <div class="offer-box">
      <p class="offer-title">Get A Free Sample Package</p>
      <p class="offer-url">www.BoldPromoPerksGroup.example</p>
    </div>
  </section>

  <section class="card card-front" aria-label="Business card, front side">
    <svg class="panel" viewBox="0 0 540 309" preserveAspectRatio="none" aria-hidden="true">
      <defs>
        <linearGradient id="panel-fill" x1="0" y1="0" x2="0" y2="1">
          <stop offset="0" stop-color="#5f89c2"/>
          <stop offset="1" stop-color="#2f5a9f"/>
        </linearGradient>
      </defs>
      <polygon points="200,0 540,0 540,309 225,309 285,120" fill="url(#panel-fill)"/>
      <polygon points="200,0 285,0 285,120" fill="#56789f"/>
    </svg>

    <div class="brand"><span class="brand-dot"></span>LVP</div>

    <div class="person">
      <h1 class="person-name">Doug Fenwick</h1>
      <p class="person-role">President</p>
      <p class="person-title">CEO</p>
    </div>

    <ul class="contacts">
      <li>1-555-302-4196
        <svg viewBox="0 0 24 24" aria-hidden="true"><path fill="#fff" d="M6.6 10.8a15 15 0 0 0 6.6 6.6l2.2-2.2c.3-.3.7-.4 1-.2 1.1.4 2.3.6 3.6.6.6 0 1 .4 1 1V20c0 .6-.4 1-1 1A17 17 0 0 1 3 4c0-.6.4-1 1-1h3.5c.6 0 1 .4 1 1 0 1.3.2 2.5.6 3.6.1.3 0 .7-.2 1z"/></svg>
      </li>
      <li>www.BoldPromoPerksGroup.example
        <svg viewBox="0 0 24 24" aria-hidden="true"><circle cx="12" cy="12" r="9" fill="none" stroke="#fff" stroke-width="2"/><path d="M3 12h18M12 3c3 3 3 15 0 18M12 3c-3 3-3 15 0 18" fill="none" stroke="#fff" stroke-width="1.6"/></svg>
      </li>
      <li>doug@boldpromoperksgroup.example
        <svg viewBox="0 0 24 24" aria-hidden="true"><rect x="2" y="5" width="20" height="14" fill="#fff"/><path d="M2 5l10 8 10-8" fill="none" stroke="#3d6eb5" stroke-width="1.6"/></svg>
      </li>
    </ul>
  </section>

</main>
</body>
</html>
```